Corvelle Meadow Organic Flower Farm, Farmer Florist

I am a flower grower and florist, so I do everything from the field to the vase. I want to include my website, phone, email and instagram

```html
<!DOCTYPE html>
<html lang="en">
<head>
<meta charset="utf-8">
<title>Corvelle Meadow — Business Cards</title>
<link href="https://fonts.googleapis.com/css2?family=Marcellus&family=Arimo:wght@400&display=swap" rel="stylesheet">
<style>
  :root{
    --bg:#1f1f1f;
    --maroon:#5e2a33;
    --maroon-text:#6b2f3a;
    --pink:#f08d93;
    --pink-light:#f4a0a5;
    --white:#ffffff;
    --ink:#3a3a3a;
    --rule:#b9a3a6;
  }
  *{box-sizing:border-box;margin:0;padding:0}
  html,body{width:1200px;height:1015px;overflow:hidden;background:var(--bg)}
  .canvas{position:relative;width:1200px;height:1015px}
  .card{position:absolute;width:580px;height:330px;overflow:hidden;box-shadow:0 18px 40px rgba(0,0,0,.55)}
  .card--front{left:80px;top:80px;background:linear-gradient(160deg,var(--pink) 0%,#b86770 45%,var(--maroon) 100%)}
  .card--back{left:540px;top:600px;background:var(--white)}

  .brand{font-family:"Marcellus",serif;color:var(--maroon-text);text-align:center;letter-spacing:.12em}
  .brand__name{font-size:40px;line-height:1;text-transform:uppercase}
  .brand__tagline{font-size:13px;margin-top:12px;letter-spacing:.22em;text-transform:uppercase}

  .card--front .brand{position:absolute;left:0;right:0;top:100px}
  .social{position:absolute;left:0;right:0;top:232px;display:flex;align-items:center;justify-content:center;gap:14px}
  .social__rule{width:150px;height:1px;background:rgba(255,220,222,.55)}
  .social__dot{width:26px;height:26px;border-radius:50%;background:var(--white)}

  .card--back .brand{position:absolute;left:28px;width:290px;top:118px}
  .card--back .brand__name{font-size:30px}
  .card--back .brand__tagline{font-size:11px}
  .divider{position:absolute;left:330px;top:70px;width:1px;height:150px;background:var(--rule)}
  .contact{position:absolute;left:352px;top:78px;font-family:"Arimo",Arial,sans-serif;color:var(--ink)}
  .contact__name{font-family:"Marcellus",serif;color:var(--maroon-text);font-size:20px;letter-spacing:.06em;text-transform:uppercase;line-height:1}
  .contact__role{font-size:14px;margin-top:4px}
  .contact__list{list-style:none;margin-top:22px}
  .contact__item{display:flex;align-items:center;gap:8px;font-size:13px;line-height:22px}
  .contact__item svg{width:14px;height:14px;fill:var(--maroon);flex:none}
  .band--maroon{position:absolute;left:0;bottom:0;width:100%;height:16px;background:var(--maroon)}
  .band--pink{position:absolute;right:0;bottom:0;width:215px;height:46px;background:var(--pink);border-left:4px solid var(--white)}
</style>
</head>
<body>
<main class="canvas">
  <section class="card card--front">
    <div class="brand">
      <div class="brand__name">Corvelle Meadow</div>
      <div class="brand__tagline">Organic Flower Farm · Est. 2019</div>
    </div>
    <div class="social">
      <span class="social__rule"></span>
      <span class="social__dot" aria-label="Instagram"></span>
      <span class="social__rule"></span>
    </div>
  </section>

  <section class="card card--back">
    <div class="brand">
      <div class="brand__name">Corvelle Meadow</div>
      <div class="brand__tagline">Organic Flower Farm · Est. 2019</div>
    </div>
    <div class="divider"></div>
    <div class="contact">
      <div class="contact__name">Adrian Hale</div>
      <div class="contact__role">Managing Director</div>
      <ul class="contact__list">
        <li class="contact__item">
          <svg viewBox="0 0 24 24"><path d="M6.6 10.8a15.5 15.5 0 0 0 6.6 6.6l2.2-2.2c.3-.3.7-.4 1-.2 1.1.4 2.3.6 3.6.6.6 0 1 .4 1 1V20c0 .6-.4 1-1 1A17 17 0 0 1 3 4c0-.6.4-1 1-1h3.5c.6 0 1 .4 1 1 0 1.3.2 2.5.6 3.6.1.3 0 .7-.2 1z"/></svg>
          044-555 018 274
        </li>
        <li class="contact__item">
          <svg viewBox="0 0 24 24"><path d="M2 5h20v14H2zm2 2v.5l8 5 8-5V7l-8 5z"/></svg>
          info@corvellemeadow.com
        </li>
        <li class="contact__item">
          <svg viewBox="0 0 24 24"><path d="M12 2a10 10 0 1 0 0 20 10 10 0 0 0 0-20zm6.9 6h-3a15 15 0 0 0-1.3-4 8 8 0 0 1 4.3 4zM12 4c.8 1.1 1.5 2.5 1.9 4h-3.8c.4-1.5 1.1-2.9 1.9-4zM4.3 14a8 8 0 0 1 0-4h3.4a16 16 0 0 0 0 4zm.8 2h3a15 15 0 0 0 1.3 4 8 8 0 0 1-4.3-4zm3-8h-3a8 8 0 0 1 4.3-4 15 15 0 0 0-1.3 4zM12 20c-.8-1.1-1.5-2.5-1.9-4h3.8c-.4 1.5-1.1 2.9-1.9 4zm2.3-6H9.7a14 14 0 0 1 0-4h4.6a14 14 0 0 1 0 4zm.3 6a15 15 0 0 0 1.3-4h3a8 8 0 0 1-4.3 4zm1.7-6a16 16 0 0 0 0-4h3.4a8 8 0 0 1 0 4z"/></svg>
          www.corvellemeadow.com
        </li>
      </ul>
    </div>
    <div class="band--maroon"></div>
    <div class="band--pink"></div>
  </section>
</main>
</body>
</html>
```